BRIVAN 2026 Flyer for Conference

BRIVAN needs a design for a 1-page flyer that we will hand out at an upcoming event & then later post online as a pdf. There are 3 elements which need to be on the flyer:

1) A logo. This should be prominent on the design (e.g., in the middle). The flyer should use the colors that are in that logo (e.g., for accents, design elements, and/or text; not all of these have to be used):
Dark blue: #185577
Med blue: #327C9A
Teal: #4EB1C2
Light Teal: #9EDBE6

2) The conference theme -- Oceans of Knowledge: Diving into Information Literacy -- should be at the flyer's top.

3) Finally, these six tracks should be listed below the theme and the logo (it's font size should be at least a couple sizes smaller than the size used for the theme):
- Pearls of Pedagogy: Teaching Techniques that Work
- The Depth Gauge: Measuring Instructional Impact
- Techtonic Shifts: Innovation and Educational Technology
- Captain's Log: Navigating Leadership in Library Instruction
- Swimming Together: Collaborating with Others
- The Bermuda Triangle: Exploring (Seemingly) Eternal Challenges

Font styles to use
Sans Serif

Colors
0094D4
00A9DD
6FCCEA
C7EBF8
E9F6FB

Requirements
Must have
• The 3 elements listed in the description: 1) the logo, 2) the text of the theme and 3) the text for the tracks.

```html
<!DOCTYPE html>
<html lang="en">
<head>
<meta charset="utf-8">
<title>BRIVAN 2026 – Oceans of Knowledge</title>
<link href="https://fonts.googleapis.com/css2?family=Montserrat:wght@500;600;700;800&display=swap" rel="stylesheet">
<style>
  :root {
    --dark-blue: #185577;
    --med-blue: #327C9A;
    --teal: #4EB1C2;
    --light-teal: #9EDBE6;
    --sea-top: #0F7AA0;
    --sea-bottom: #0A6A90;
    --white: #FFFFFF;
  }
  * { margin: 0; padding: 0; box-sizing: border-box; }
  html, body { width: 927px; height: 1200px; overflow: hidden; background: var(--white); }
  .flyer {
    position: relative;
    width: 927px;
    height: 1200px;
    overflow: hidden;
    font-family: "Montserrat", sans-serif;
    background: var(--white);
  }
  .flyer__backdrop { position: absolute; inset: 0; }
  .top-band { position: absolute; left: 0; top: 0; width: 100%; height: 16px; background: var(--light-teal); }

  .brand {
    position: absolute;
    left: 0; right: 0; top: 130px;
    display: flex; justify-content: center; align-items: center; gap: 18px;
  }
  .brand__dot { width: 46px; height: 46px; border-radius: 50%; background: var(--teal); }
  .brand__name {
    font-family: "Montserrat", sans-serif;
    font-weight: 800;
    font-size: 72px;
    letter-spacing: 2px;
    color: var(--dark-blue);
  }

  .theme { position: absolute; left: 0; top: 0; }
  .theme__title { font-family: "Montserrat", sans-serif; font-weight: 800; font-size: 62px; fill: var(--teal); }
  .theme__subtitle { font-family: "Montserrat", sans-serif; font-weight: 800; font-size: 54px; fill: var(--dark-blue); }

  .divider { position: absolute; background: var(--white); }
  .divider--vertical { left: 457px; top: 574px; width: 1.4px; height: 601px; }
  .divider--row { height: 1.4px; }

  .track {
    position: absolute;
    width: 380px;
    text-align: center;
    color: var(--white);
  }
  .track--left { left: -2px; }
  .track--right { left: 537px; }
  .track__icon {
    display: block;
    width: 70px; height: 66px;
    margin: 0 auto 20px;
    border-radius: 10px;
    background: rgba(255, 255, 255, 0.85);
  }
  .track__title { font-weight: 700; font-size: 27px; line-height: 34px; letter-spacing: 0.2px; }
  .track__desc { font-weight: 500; font-size: 19px; line-height: 26px; margin-top: 6px; }
</style>
</head>
<body>
<main class="flyer">
  <svg class="flyer__backdrop" width="927" height="1200" viewBox="0 0 927 1200" aria-hidden="true">
    <defs>
      <linearGradient id="sea" x1="0" y1="0" x2="0" y2="1">
        <stop offset="0" stop-color="var(--sea-top)"/>
        <stop offset="1" stop-color="var(--sea-bottom)"/>
      </linearGradient>
    </defs>
    <rect x="0" y="380" width="927" height="820" fill="url(#sea)" role="img" aria-label="Rippling sea water texture"/>
    <path d="M0,402 Q463,669 927,407" fill="none" stroke="var(--teal)" stroke-width="15"/>
    <path d="M0,0 H927 V400 Q463,662 0,395 Z" fill="var(--white)"/>
  </svg>

  <div class="top-band"></div>

  <div class="brand">
    <span class="brand__name">BRIVAN 2026</span>
    <span class="brand__dot"></span>
  </div>

  <svg class="theme" width="927" height="560" viewBox="0 0 927 560">
    <defs>
      <path id="theme-title-arc" d="M50,322 Q470,499 895,300"/>
      <path id="theme-subtitle-arc" d="M15,360 Q463,574 910,352"/>
    </defs>
    <text class="theme__title">
      <textPath href="#theme-title-arc" startOffset="50%" text-anchor="middle" textLength="830" lengthAdjust="spacingAndGlyphs">OCEANS OF KNOWLEDGE</textPath>
    </text>
    <text class="theme__subtitle">
      <textPath href="#theme-subtitle-arc" startOffset="50%" text-anchor="middle" textLength="880" lengthAdjust="spacingAndGlyphs">Diving into Information Literacy</textPath>
    </text>
  </svg>

  <div class="divider divider--vertical"></div>
  <div class="divider divider--row" style="left:388px; top:671px; width:145px;"></div>
  <div class="divider divider--row" style="left:372px; top:858px; width:181px;"></div>
  <div class="divider divider--row" style="left:373px; top:1073px; width:152px;"></div>

  <section class="track track--left" style="top:560px;">
    <span class="track__icon" role="img" aria-label="Icon of a teacher presenting at a board"></span>
    <h2 class="track__title">Pearls of Pedagogy</h2>
    <p class="track__desc">Teaching Techniques that Work</p>
  </section>

  <section class="track track--right" style="top:552px;">
    <span class="track__icon" role="img" aria-label="Icon of a blueprint with measurements" style="margin-bottom:28px;"></span>
    <h2 class="track__title">The Depth Gauge</h2>
    <p class="track__desc">Measuring Instructional Impact</p>
  </section>

  <section class="track track--left" style="top:753px;">
    <span class="track__icon" role="img" aria-label="Icon of a connected network sphere" style="width:70px;height:70px;border-radius:50%;margin-bottom:22px;"></span>
    <h2 class="track__title">Techtonic Shifts</h2>
    <p class="track__desc">Innovation and Educational<br>Technology</p>
  </section>

  <section class="track track--right" style="top:750px;">
    <span class="track__icon" role="img" aria-label="Icon of a leader with a team" style="width:72px;height:72px;margin-bottom:22px;"></span>
    <h2 class="track__title">Captain's Log</h2>
    <p class="track__desc">Navigating Leadership in<br>Library Instruction</p>
  </section>

  <section class="track track--left" style="top:984px;">
    <span class="track__icon" role="img" aria-label="Icon of a swimmer in waves" style="width:82px;height:60px;margin-bottom:28px;"></span>
    <h2 class="track__title">Swimming Together</h2>
    <p class="track__desc">Collaborating with Others</p>
  </section>

  <section class="track track--right" style="top:978px;">
    <span class="track__icon" role="img" aria-label="Icon of a route map with a plane and a ship" style="width:64px;height:64px;margin-bottom:30px;"></span>
    <h2 class="track__title">The Bermuda Triangle</h2>
    <p class="track__desc">Exploring (Seemingly)<br>Eternal Challenges</p>
  </section>
</main>
</body>
</html>
```